Disposable Mini Sauce Pot Design for Asian Chain Food Brands

We operate a Hainan Chicken Rice takeout brand under the name Brindle4U, with our official website: www.Brindle4U.example.
We offer four signature house sauces and are launching brand-new packaging for our sauce line. We require custom graphic designs exclusively for the sauce cup lids.
Product Material & Base Specs
The sauce cups are made of PP plastic, available in two translucent base options: Translucent White and Translucent Orange.
Four Sauce Varieties for Individual Lid Designs
1. Red Sauce – Fried Sweet Chili Sauce
2.Green Sauce – Scallion Oil Dressing
3.Sweet Soy Sauce
4.Sweet Red Sauce (Special for Fried Chicken)
Differentiate each sauce lid design through unique graphics, typography, or illustrative elements for easy customer identification.
The marking NET WT 2 OZ must be clearly printed on every lid.
**There is no need to print full descriptive text or the full name of the sauces on each lid; the design only needs to clearly differentiate the four sauce varieties.
**Please reference the original design style and brand color palette shown on our official website, and feel free to fully unleash your creativity.
Look and feel
Each slider illustrates characteristics of the customer's brand and the style your logo design should communicate.

```html
<!DOCTYPE html>
<html lang="en">
<head>
<meta charset="utf-8">
<title>Brindle4U Sauce Lids</title>
<link rel="stylesheet" href="https://fonts.googleapis.com/css2?family=Montserrat:wght@800;900&display=swap">
<style>
  :root {
    --page: #fafafa;
    --lid: #000000;
    --cream: #f8e8ab;
    --white: #ffffff;
    --red: #e10015;
    --orange: #e07000;
    --green: #6bb32e;
    --pink: #f4ab96;
  }
  html, body {
    margin: 0;
    padding: 0;
    width: 1072px;
    height: 1200px;
    overflow: hidden;
    background: var(--page);
  }
  .sheet {
    position: relative;
    width: 1072px;
    height: 1200px;
  }
  .lid {
    position: absolute;
    width: 450px;
    height: 509px;
    font-family: "Montserrat", sans-serif;
  }
  .lid--red { left: 79px; top: 70px; }
  .lid--sweet-red { left: 551px; top: 70px; }
  .lid--green { left: 79px; top: 624px; }
  .lid--soy { left: 551px; top: 624px; }
  .lid-base { fill: var(--lid); }
  .word-big { font-weight: 900; fill: var(--cream); }
  .word-sauce { font-weight: 900; }
  .tint-red { fill: var(--red); }
  .tint-orange { fill: var(--orange); }
  .tint-green { fill: var(--green); }
  .tint-pink { fill: var(--pink); }
  .net-wt, .flavour-note, .brand-name {
    font-weight: 800;
    fill: var(--white);
  }
  .net-wt { font-size: 30px; }
  .flavour-note { font-size: 29px; }
  .brand-name { font-size: 40px; }
</style>
</head>
<body>
<main class="sheet">

  <!-- Red sauce -->
  <svg class="lid lid--red" viewBox="0 0 760 860" aria-label="Red sauce lid">
    <defs><clipPath id="clip-red"><rect width="760" height="860" rx="120"/></clipPath></defs>
    <rect class="lid-base" width="760" height="860" rx="120"/>
    <rect class="tint-red" x="97" y="0" width="575" height="95" clip-path="url(#clip-red)" role="img" aria-label="Red sauce dripping from the lid edge"/>
    <text class="word-big" x="87" y="562" font-size="612" textLength="385" lengthAdjust="spacingAndGlyphs">R</text>
    <text class="word-big" x="494" y="357" font-size="312" textLength="168" lengthAdjust="spacingAndGlyphs">E</text>
    <text class="word-big" x="494" y="565" font-size="276" textLength="191" lengthAdjust="spacingAndGlyphs">D</text>
    <text class="word-sauce tint-red" x="82" y="694" font-size="210" textLength="593" lengthAdjust="spacingAndGlyphs">sauce</text>
    <text class="net-wt" x="495" y="732" textLength="160" lengthAdjust="spacingAndGlyphs">NET WT 2 OZ</text>
    <text class="flavour-note" x="37" y="781">FRIED SWEET</text>
    <text class="flavour-note" x="37" y="809">CHILI SAUCE</text>
    <text class="brand-name" x="564" y="800" textLength="169" lengthAdjust="spacingAndGlyphs">Brindle4U</text>
  </svg>

  <!-- Sweet red sauce -->
  <svg class="lid lid--sweet-red" viewBox="0 0 760 860" aria-label="Sweet red sauce lid">
    <defs><clipPath id="clip-sweet-red"><rect width="760" height="860" rx="120"/></clipPath></defs>
    <rect class="lid-base" width="760" height="860" rx="120"/>
    <rect class="tint-orange" x="97" y="0" width="575" height="95" clip-path="url(#clip-sweet-red)" role="img" aria-label="Orange sauce dripping from the lid edge"/>
    <text class="word-big" x="87" y="562" font-size="612" textLength="385" lengthAdjust="spacingAndGlyphs">R</text>
    <text class="word-big" x="494" y="357" font-size="312" textLength="168" lengthAdjust="spacingAndGlyphs">E</text>
    <text class="word-big" x="494" y="565" font-size="276" textLength="191" lengthAdjust="spacingAndGlyphs">D</text>
    <text class="word-sauce tint-orange" transform="translate(174 542) rotate(-90)" font-size="130" textLength="378" lengthAdjust="spacingAndGlyphs">sweet</text>
    <text class="word-sauce tint-orange" x="82" y="694" font-size="210" textLength="593" lengthAdjust="spacingAndGlyphs">sauce</text>
    <text class="net-wt" x="495" y="732" textLength="160" lengthAdjust="spacingAndGlyphs">NET WT 2 OZ</text>
    <text class="flavour-note" x="37" y="783">SPECIAL FOR</text>
    <text class="flavour-note" x="37" y="811">FRIED CHICKEN</text>
    <text class="brand-name" x="564" y="800" textLength="169" lengthAdjust="spacingAndGlyphs">Brindle4U</text>
  </svg>

  <!-- Green sauce -->
  <svg class="lid lid--green" viewBox="0 0 760 860" aria-label="Green sauce lid">
    <defs><clipPath id="clip-green"><rect width="760" height="860" rx="120"/></clipPath></defs>
    <rect class="lid-base" width="760" height="860" rx="120"/>
    <rect class="tint-green" x="97" y="0" width="575" height="95" clip-path="url(#clip-green)" role="img" aria-label="Green sauce dripping from the lid edge"/>
    <text class="word-big" x="63" y="520" font-size="505" textLength="350" lengthAdjust="spacingAndGlyphs">G</text>
    <text class="word-big" x="430" y="520" font-size="700" textLength="215" lengthAdjust="spacingAndGlyphs">r</text>
    <text class="word-big" transform="translate(682 525) rotate(-90)" font-size="118" textLength="215" lengthAdjust="spacingAndGlyphs">een</text>
    <text class="word-sauce tint-green" x="82" y="660" font-size="200" textLength="593" lengthAdjust="spacingAndGlyphs">sauce</text>
    <text class="net-wt" x="495" y="700" textLength="160" lengthAdjust="spacingAndGlyphs">NET WT 2 OZ</text>
    <text class="flavour-note" x="37" y="782">SCALLION OIL</text>
    <text class="flavour-note" x="37" y="810">DRESSING</text>
    <text class="brand-name" x="564" y="800" textLength="169" lengthAdjust="spacingAndGlyphs">Brindle4U</text>
  </svg>

  <!-- Sweet soy sauce -->
  <svg class="lid lid--soy" viewBox="0 0 760 860" aria-label="Sweet soy sauce lid">
    <defs><clipPath id="clip-soy"><rect width="760" height="860" rx="120"/></clipPath></defs>
    <rect class="lid-base" width="760" height="860" rx="120"/>
    <rect class="tint-pink" x="97" y="0" width="575" height="95" clip-path="url(#clip-soy)" role="img" aria-label="Soy sauce dripping from the lid edge"/>
    <text class="word-big" x="82" y="360" font-size="420" textLength="589" lengthAdjust="spacingAndGlyphs">sw</text>
    <text class="word-big" x="82" y="598" font-size="320" textLength="586" lengthAdjust="spacingAndGlyphs">eet</text>
    <text class="word-big" transform="translate(138 700) rotate(-90)" font-size="80" textLength="97" lengthAdjust="spacingAndGlyphs">soy</text>
    <text class="word-sauce tint-pink" x="141" y="702" font-size="190" textLength="529" lengthAdjust="spacingAndGlyphs">sauce</text>
    <text class="net-wt" x="495" y="738" textLength="160" lengthAdjust="spacingAndGlyphs">NET WT 2 OZ</text>
    <text class="brand-name" x="564" y="800" textLength="169" lengthAdjust="spacingAndGlyphs">Brindle4U</text>
  </svg>

</main>
</body>
</html>
```